Willow Cradle Pregnancy and Baby Massage

I need a web design for a new business, WILLOW CRADLE PREGNANCY AND BABY MASSAGE that I am in the process of setting up in the suburbs of Perth, Western Australia. The business is owned and operated by myself and my intention is to service Pregnant Mothers and Parents of Young Babies that would benefit from massage. I would like to have a "Home Page" and pages for "About Me", "Pregnancy Massage", "Baby Massage", a Pricing Page for Pregnancy Massage Sessions, a Pricing Page for Baby Massage Sessions, and a "Contact Me" page to allow clients to either contact me with queries or book available pregnancy massage sessions on a particular day of the week. I would also like a "News" page that would include articles I have written, news about new courses and a link to my Circlebook page (yet to be set up). I would like to keep the colour schemes similar to my logo design colours. I need the design to be easy to follow and to appeal to a younger audience (20's to mid 30's).
The target audience is pregnant mothers-to-be wishing to receive massage treatments, and new parents and grandparents of small babies that would like to learn how to massage their babies.
The look and feel should be modern, professional, elegant and feminine.
I need the design to be in a standard format such that I can update the content by myself ( and does not need specialised software) as the company and business progresses.

Target Market(s)

Contact Information for Business Card

Card should have rounded edges. Design should have the same "feel" as the website. Contact Details of my business address, mobile phone, email and website should be included.

Font styles to use
Script

Requirements
Must have
• Same colours as logo design. In cmyk system, the colours are: 20,60,0,0 which best result is pantone 681 and 40,40,0,0 which best result is pantone 2645. Card should include the logo design.

```html
<!DOCTYPE html>
<html lang="en">
<head>
<meta charset="utf-8">
<title>Willow Cradle Pregnancy and Baby Massage</title>
<link rel="stylesheet" href="https://fonts.googleapis.com/css2?family=Questrial&family=Open+Sans:wght@400&display=swap">
<style>
  :root {
    --nav-bg: rgba(52, 50, 52, 0.92);
    --nav-text: #d9d6da;
    --white: #ffffff;
    --ink: #444247;
    --plum: #8a4f96;
    --lilac: #b7a3d0;
    --orchid: #e2c5e0;
    --blush: #f6e7ee;
    --footer: #4f4673;
    --footer-text: #e4e0ee;
  }
  * { margin: 0; padding: 0; box-sizing: border-box; }
  html, body { width: 930px; height: 1200px; overflow: hidden; background: var(--white); }
  body { position: relative; font-family: "Questrial", sans-serif; color: var(--ink); }

  .hero { position: absolute; left: 0; top: 0; width: 930px; height: 540px; overflow: hidden; }
  .hero-photo {
    position: absolute; inset: 0;
    background:
      radial-gradient(ellipse 260px 230px at 610px 250px, #e49a82 0%, #c9857a 45%, rgba(150,105,110,0) 100%),
      radial-gradient(ellipse 320px 300px at 640px 200px, #d8c4b8 0%, rgba(170,140,140,0) 80%),
      linear-gradient(100deg, #6d5558 0%, #8c6f73 40%, #9a7f86 70%, #8a6e7a 100%);
  }
  .hero-waves { position: absolute; left: 0; top: 420px; width: 930px; height: 120px; }

  .site-nav {
    position: absolute; left: 0; top: 0; width: 930px; height: 32px;
    background: var(--nav-bg);
  }
  .site-nav a {
    position: absolute; top: 9px; font-size: 10.4px; color: var(--nav-text);
    text-decoration: none; white-space: nowrap;
  }
  .site-nav a.current { color: var(--white); text-decoration: underline; }

  .brand-card {
    position: absolute; left: 102px; top: 0; width: 219px; height: 138px;
    background: var(--white); border-radius: 0 0 16px 16px;
    box-shadow: 0 2px 6px rgba(0,0,0,0.18);
  }
  .brand-card::after {
    content: ""; position: absolute; left: 6px; right: 6px; top: -2px; bottom: 6px;
    border: 1px dashed #6b6b6b; border-top: none; border-radius: 0 0 11px 11px;
  }
  .brand-name {
    position: absolute; left: 18px; right: 18px; top: 36px;
    display: flex; flex-direction: column; align-items: center; gap: 8px;
    color: var(--plum); font-size: 17px; line-height: 21px; text-align: center;
  }
  .brand-dot { width: 22px; height: 22px; border-radius: 50%; background: var(--plum); }

  .slide-arrow { position: absolute; top: 243px; width: 16px; height: 24px; }
  .slide-arrow.prev { left: 29px; }
  .slide-arrow.next { left: 890px; }

  .hero-caption {
    position: absolute; left: 103px; top: 287px; width: 275px;
    color: var(--white); font-size: 14.4px; line-height: 21px;
  }

  .vision-photo-frame {
    position: absolute; left: 105px; top: 580px; width: 300px; height: 300px;
    border-radius: 50%; border: 1px dashed #555;
  }
  .vision-photo {
    position: absolute; left: 11px; top: 11px; width: 278px; height: 278px; border-radius: 50%;
    background: radial-gradient(circle at 45% 45%, #f6c8b4 0%, #eab29e 40%, #d9c7bf 75%, #cfc6c4 100%);
  }
  .vision-text { position: absolute; left: 465px; top: 613px; width: 370px; font-size: 14px; line-height: 21px; }
  .vision-text p + p { margin-top: 21px; }

  .trust-band {
    position: absolute; left: 0; top: 952px; width: 930px; height: 161px;
    background: radial-gradient(ellipse at 70% 50%, #fbeff4 0%, var(--blush) 60%, #f3dce6 100%);
  }
  .certificate-badge {
    position: absolute; left: 112px; top: 24px; width: 196px; height: 116px;
    border-radius: 10px; background: rgba(226, 197, 224, 0.55);
  }
  .social-follow { position: absolute; left: 740px; top: 52px; width: 105px; text-align: center; font-size: 12px; color: #333; }
  .social-link { display: flex; align-items: center; justify-content: center; gap: 5px; margin-top: 10px; color: var(--footer); font-size: 12px; }
  .social-link span.dot { width: 9px; height: 9px; border-radius: 50%; background: var(--footer); }

  .site-footer {
    position: absolute; left: 0; top: 1113px; width: 930px; height: 87px;
    background: var(--footer); color: var(--footer-text);
    font-family: "Open Sans", sans-serif; font-size: 9px; text-align: center;
  }
  .footer-links { margin-top: 25px; }
  .footer-links a { color: var(--footer-text); text-decoration: none; }
  .footer-links .sep { margin: 0 6px; }
  .copyright { margin-top: 9px; }
</style>
</head>
<body>
  <header class="hero">
    <div class="hero-photo" role="img" aria-label="Photograph of two sleeping newborn babies wrapped in a coral blanket on a lace heart"></div>
    <svg class="hero-waves" viewBox="0 0 930 120" preserveAspectRatio="none" aria-hidden="true">
      <path d="M0 95 C 120 40, 220 20, 330 30 C 480 45, 600 100, 720 88 C 800 80, 870 40, 930 12 L930 120 L0 120 Z" fill="var(--lilac)"/>
      <path d="M0 105 C 120 70, 220 50, 330 50 C 470 55, 560 100, 700 92 C 800 86, 880 60, 930 45 L930 120 L0 120 Z" fill="var(--orchid)"/>
      <path d="M0 106 C 80 80, 160 62, 260 60 C 420 58, 560 95, 710 88 C 800 84, 880 100, 930 118 L930 120 L0 120 Z" fill="var(--white)"/>
    </svg>

    <nav class="site-nav">
      <a class="current" href="#" style="left:367px">Home</a>
      <a href="#" style="left:414px">About Me</a>
      <a href="#" style="left:478px">Pregnancy Massage</a>
      <a href="#" style="left:590px">Baby Massage</a>
      <a href="#" style="left:678px">Pricing</a>
      <a href="#" style="left:730px">News</a>
      <a href="#" style="left:775px">Contact Me</a>
    </nav>

    <div class="brand-card">
      <div class="brand-name"><span class="brand-dot"></span>Willow Cradle Pregnancy and Baby Massage</div>
    </div>

    <svg class="slide-arrow prev" viewBox="0 0 16 24" aria-label="Previous slide"><path d="M12 3 L4 12 L12 21" fill="none" stroke="#fff" stroke-width="3"/></svg>
    <svg class="slide-arrow next" viewBox="0 0 16 24" aria-label="Next slide"><path d="M4 3 L12 12 L4 21" fill="none" stroke="#fff" stroke-width="3"/></svg>

    <p class="hero-caption">Willow Cradle Pregnancy and Baby Massage was launched in 2017, offering massage for pregnant women, and instruction of baby massage to parents, grandparents and carers.</p>
  </header>

  <main>
    <div class="vision-photo-frame">
      <div class="vision-photo" role="img" aria-label="Photograph of a newborn's feet resting in a parent's hand"></div>
    </div>
    <div class="vision-text">
      <p>My vision is to provide a professional massage service to pregnant mothers and babies that also benefits from my skills and experience as a midwife.</p>
      <p>My expectation is that after each session, my clients should leave feeling relaxed, calm, emotionally nurtured, soothed and supported.</p>
      <p>At all times, I will take the utmost care of your privacy, safety and comfort in what is a very personal, intimate time in your life.</p>
    </div>
  </main>

  <section class="trust-band">
    <div class="certificate-badge" role="img" aria-label="Certification badge"></div>
    <div class="social-follow">
      Follow us on
      <a class="social-link" href="#"><span class="dot"></span>Circlebook</a>
    </div>
  </section>

  <footer class="site-footer">
    <div class="footer-links">
      <a href="#">Home</a><span class="sep">|</span><a href="#">About Me</a><span class="sep">|</span><a href="#">Pregnancy Massage</a><span class="sep">|</span><a href="#">Baby Massage</a><span class="sep">|</span><a href="#">Pricing</a><span class="sep">|</span><a href="#">News</a><span class="sep">|</span><a href="#">Contact Me</a>
    </div>
    <p class="copyright">Copyright &copy; 2017 Willow Cradle Pregnancy &amp; Baby Massage. &nbsp;All rights reserved.</p>
  </footer>
</body>
</html>
```